Quarrelsome Harbor - a feature film documentary poster

Please help me design the poster for a documentary feature film I am making called, "Quarrelsome Harbor."

We follow Velmoran League candidate Dorian Kettle's bid for President of the United States as he drives around the country in a coffin shaped bus, arriving at campaign events such as biohacking labs, cryopreservation sites, Transhuman churches, and ending at the nation's capital to deliver a Pellucid Accord of Claims.

Possible tag lines: Hitchhike into the future, Living forever now, One man's journey into the future, Surfing the Techpocalypse

Target Market(s)

Documentary filmgoers. NRV watchers. People interested in technology and the future.

Industry/Entity Type

Film Production

Font styles to use
Sans Serif

Requirements
Must have
• Dorian
Nice to have
• Work in the fact Dorian is running for president.

```html
<!DOCTYPE html>
<html lang="en">
<head>
<meta charset="utf-8">
<title>Quarrelsome Harbor — Documentary Poster</title>
<link rel="stylesheet" href="https://fonts.googleapis.com/css2?family=Josefin+Sans:wght@600;700&family=Special+Elite&display=swap">
<style>
  :root {
    --stripe-amber: #e6b12a;
    --stripe-gold: #f0cf3a;
    --canton: #d2bd36;
    --star: #edd246;
    --title: #d6602c;
    --scene-sky: #e9c64a;
    --scene-bus: #a57a3c;
    --scene-ground: #8a6c3e;
    --scene-shadow: #5e4d30;
    --bus-lettering: #ecdcb4;
  }
  html, body {
    margin: 0;
    padding: 0;
    width: 810px;
    height: 1200px;
    overflow: hidden;
    background: var(--stripe-gold);
  }
  .poster {
    position: relative;
    width: 810px;
    height: 1200px;
    overflow: hidden;
  }
  .flag-field {
    position: absolute;
    inset: 0;
    display: block;
  }
  .title-block {
    position: absolute;
    inset: 0;
    margin: 0;
    font-family: "Josefin Sans", sans-serif;
    font-weight: 700;
    color: var(--title);
    text-align: center;
    text-transform: uppercase;
    pointer-events: none;
  }
  .title-line {
    position: absolute;
    left: 0;
    right: 0;
    line-height: 1;
  }
  .title-primary {
    top: 380px;
    font-size: 86px;
    letter-spacing: 3px;
  }
  .title-secondary {
    top: 628px;
    font-size: 82px;
    letter-spacing: 4px;
  }
  .bus-lettering {
    position: absolute;
    margin: 0;
    font-family: "Special Elite", "Courier New", monospace;
    color: var(--bus-lettering);
    text-transform: uppercase;
    line-height: 1;
    white-space: nowrap;
  }
  .bus-name {
    left: 262px;
    top: 1075px;
    font-size: 13px;
    letter-spacing: 3px;
  }
  .bus-candidate {
    left: 470px;
    top: 1070px;
    font-size: 9px;
    letter-spacing: 0.5px;
  }
  .bus-web {
    left: 490px;
    top: 1082px;
    font-size: 7px;
    text-transform: none;
  }
</style>
</head>
<body>
<main class="poster">
  <svg class="flag-field" width="810" height="1200" viewBox="0 0 810 1200">
    <defs>
      <polygon id="star" points="0,-30 7,-9.5 28.5,-9.3 11.3,3.6 17.6,24.3 0,12 -17.6,24.3 -11.3,3.6 -28.5,-9.3 -7,-9.5" fill="var(--star)"/>
      <linearGradient id="sceneTone" x1="0" y1="0" x2="0" y2="1">
        <stop offset="0" stop-color="var(--scene-sky)" stop-opacity="0"/>
        <stop offset="0.2" stop-color="var(--scene-sky)"/>
        <stop offset="0.4" stop-color="var(--scene-bus)"/>
        <stop offset="0.75" stop-color="var(--scene-ground)"/>
        <stop offset="1" stop-color="var(--scene-shadow)"/>
      </linearGradient>
    </defs>

    <g class="stripes">
      <rect x="0" y="0" width="810" height="92.3" fill="var(--stripe-amber)"/>
      <rect x="0" y="92.3" width="810" height="92.3" fill="var(--stripe-gold)"/>
      <rect x="0" y="184.6" width="810" height="92.3" fill="var(--stripe-amber)"/>
      <rect x="0" y="276.9" width="810" height="92.3" fill="var(--stripe-gold)"/>
      <rect x="0" y="369.2" width="810" height="92.3" fill="var(--stripe-amber)"/>
      <rect x="0" y="461.5" width="810" height="92.3" fill="var(--stripe-gold)"/>
      <rect x="0" y="553.8" width="810" height="92.3" fill="var(--stripe-amber)"/>
      <rect x="0" y="646.1" width="810" height="92.3" fill="var(--stripe-gold)"/>
      <rect x="0" y="738.4" width="810" height="92.3" fill="var(--stripe-amber)"/>
      <rect x="0" y="830.7" width="810" height="92.3" fill="var(--stripe-gold)"/>
      <rect x="0" y="923" width="810" height="92.3" fill="var(--stripe-amber)"/>
      <rect x="0" y="1015.3" width="810" height="92.3" fill="var(--stripe-gold)"/>
      <rect x="0" y="1107.6" width="810" height="92.4" fill="var(--stripe-amber)"/>
    </g>

    <rect class="canton" x="0" y="0" width="413" height="646" fill="var(--canton)"/>

    <g class="canton-stars">
      <use href="#star" x="35" y="63"/><use href="#star" x="185" y="63"/><use href="#star" x="338" y="63"/>
      <use href="#star" x="111" y="127"/><use href="#star" x="260" y="127"/>
      <use href="#star" x="35" y="191"/><use href="#star" x="185" y="191"/><use href="#star" x="338" y="191"/>
      <use href="#star" x="111" y="255"/><use href="#star" x="260" y="255"/>
      <use href="#star" x="35" y="319"/><use href="#star" x="185" y="319"/><use href="#star" x="338" y="319"/>
      <use href="#star" x="111" y="384"/><use href="#star" x="260" y="384"/>
      <use href="#star" x="35" y="448"/><use href="#star" x="185" y="448"/><use href="#star" x="338" y="448"/>
      <use href="#star" x="111" y="512"/><use href="#star" x="260" y="512"/>
      <use href="#star" x="35" y="577"/><use href="#star" x="185" y="577"/><use href="#star" x="338" y="577"/>
    </g>

    <rect class="road-scene" x="0" y="940" width="810" height="260" fill="url(#sceneTone)"
          role="img" aria-label="Photograph: Dorian Kettle standing on the roof of his presidential campaign bus, parked in desert scrub with mountains on the horizon"/>
  </svg>

  <h1 class="title-block">
    <span class="title-line title-primary">Quarrelsome</span>
    <span class="title-line title-secondary">Harbor</span>
  </h1>

  <p class="bus-lettering bus-name">Quarrelsome Bus</p>
  <p class="bus-lettering bus-candidate">Velmoran League Dorian Kettle</p>
  <p class="bus-lettering bus-web">www.kettleforpresident.org</p>
</main>
</body>
</html>
```